Beef cattle farm needs signs which can be seen from roadside

We would like submissions of artwork for a sign that will hang from a fence or gate and will be seen by passing cars.

Existing logo and branding theme for the company is attached.

Signage can be between 900mm x 400mm - 1200mm x 600mm

Industry/Entity Type

Farm

Requirements
Must have
• the Signs should have the following information:
• Company name: Wendlow Grazing Company
• Address: 417 Corrigan Flat Road
• Contact number: 0431 862 407
• email address: admin@wendlowgrazingcompany.com.au
• - Logo and branding as per attached artwork

```html
<!DOCTYPE html>
<html lang="en">
<head>
<meta charset="utf-8">
<title>Wendlow Grazing Company – Roadside Sign</title>
<link rel="stylesheet" href="https://fonts.googleapis.com/css2?family=Montserrat:wght@500&family=Arimo:wght@400;700&display=swap">
<style>
  :root {
    --backdrop: #868684;
    --sign-white: #ffffff;
    --brand-green: #175c37;
    --band-dark: #083a1f;
    --band-light: #136b38;
    --swoosh-grey: #9a9a9c;
    --text-white: #ffffff;
  }
  * { margin: 0; padding: 0; box-sizing: border-box; }
  html, body {
    width: 1200px;
    height: 655px;
    overflow: hidden;
    background: var(--backdrop);
  }
  .sign {
    position: absolute;
    left: 109px;
    top: 109px;
    width: 981px;
    height: 436px;
    background: var(--sign-white);
    overflow: hidden;
  }
  .sign__wave {
    position: absolute;
    inset: 0;
    width: 981px;
    height: 436px;
  }
  .brand-mark {
    position: absolute;
    left: 66px;
    top: 31px;
    width: 270px;
    height: 270px;
    border-radius: 50%;
    background: var(--brand-green);
  }
  .brand-name {
    position: absolute;
    left: 372px;
    top: 58px;
    color: var(--brand-green);
    font-family: "Montserrat", sans-serif;
    font-weight: 500;
    line-height: 1;
  }
  .brand-name__main {
    display: block;
    font-size: 96px;
    letter-spacing: 1px;
  }
  .brand-name__sub {
    display: block;
    margin-top: 18px;
    font-size: 41px;
    letter-spacing: 0.5px;
  }
  .contact {
    position: absolute;
    color: var(--text-white);
    font-family: "Arimo", sans-serif;
    white-space: nowrap;
  }
  .contact--phone {
    right: 44px;
    top: 342px;
    font-size: 28px;
    font-weight: 700;
  }
  .contact--email {
    right: 42px;
    top: 385px;
    font-size: 19.5px;
    font-weight: 700;
  }
  .contact--address {
    left: 63px;
    top: 388px;
    font-size: 22px;
    font-weight: 400;
  }
</style>
</head>
<body>
  <div class="sign">
    <svg class="sign__wave" viewBox="0 0 981 436" aria-hidden="true">
      <defs>
        <linearGradient id="band-gradient" x1="0" y1="0" x2="1" y2="0">
          <stop offset="0" stop-color="var(--band-dark)"/>
          <stop offset="0.45" stop-color="#0f5a30"/>
          <stop offset="1" stop-color="var(--band-light)"/>
        </linearGradient>
        <linearGradient id="swoosh-gradient" x1="0" y1="0" x2="1" y2="0">
          <stop offset="0" stop-color="#e4e4e4"/>
          <stop offset="1" stop-color="var(--swoosh-grey)"/>
        </linearGradient>
      </defs>
      <path class="wave__swoosh" fill="url(#swoosh-gradient)"
            d="M0,300 C150,346 300,346 520,300 S850,238 981,258 V436 H0 Z"/>
      <path class="wave__band" fill="url(#band-gradient)"
            d="M0,312 C150,352 300,352 520,306 S850,256 981,276 V436 H0 Z"/>
    </svg>

    <div class="brand-mark" aria-hidden="true"></div>

    <h1 class="brand-name">
      <span class="brand-name__main">WENDLOW</span>
      <span class="brand-name__sub">GRAZING COMPANY</span>
    </h1>

    <p class="contact contact--phone">Call : 0431 862 407</p>
    <p class="contact contact--email">admin@wendlowgrazingcompany.com.au</p>
    <p class="contact contact--address">417 Corrigan Flat Road</p>
  </div>
</body>
</html>
```